Boutique custom software development company needs new business card

Our nearly 20 year old custom software development company would like to better include the fact that we are now providing Bitcoin services. These new services are B2B include education (how to acquire and securely hold Bitcoin) and integrating Bitcoin payments into existing ecommerce sites or other existing systems. Please keep the card clean and simple. Attached is our current design and some other files. vextorial.com

Target Market(s)

businesses owners interested in long term relationship

Industry/Entity Type

Custom software development and Bitcoin

Contact Information for Business Card

Dale Parker, dale@vextorial.com, vextorial.com, (888) 555-VXTRL

Font styles to use
Other font styles liked:
• monospace

Requirements
Must have
• double-sided
Nice to have
• clean and simple
Should not have
• physical address

```html
<!DOCTYPE html>
<html lang="en">
<head>
<meta charset="utf-8">
<title>Vextorial — Business Card</title>
<link href="https://fonts.googleapis.com/css2?family=Lato:wght@400;700;900&display=swap" rel="stylesheet">
<style>
  :root {
    --backdrop: #dcdcdc;
    --paper: #ffffff;
    --brand-blue: #2f72c4;
    --brand-orange: #f57d16;
    --ink-grey: #5a5a5a;
    --soft-white: rgba(255,255,255,0.85);
  }
  * { margin: 0; padding: 0; box-sizing: border-box; }
  html, body { width: 1200px; height: 1056px; overflow: hidden; }
  body {
    background: var(--backdrop);
    font-family: "Lato", sans-serif;
    position: relative;
  }
  .card {
    position: absolute;
    left: 180px;
    width: 840px;
    height: 480px;
    box-shadow: 0 6px 18px rgba(0,0,0,0.12);
    overflow: hidden;
  }
  .card--front { top: 40px; background: var(--paper); }
  .card--back { top: 536px; background: var(--brand-blue); }

  /* Front */
  .brand {
    position: absolute;
    left: 70px;
    top: 170px;
  }
  .brand__row { display: flex; align-items: center; gap: 14px; }
  .brand__square { width: 26px; height: 26px; background: var(--brand-orange); }
  .brand__name {
    font-weight: 900;
    font-size: 64px;
    line-height: 1;
    color: var(--brand-blue);
    letter-spacing: 0.5px;
  }
  .brand__tagline {
    margin-top: 10px;
    font-size: 21px;
    color: var(--brand-blue);
  }
  .brand__services {
    margin-top: 6px;
    font-size: 21px;
    color: var(--brand-orange);
  }
  .contact {
    position: absolute;
    left: 470px;
    top: 150px;
  }
  .contact__name {
    font-weight: 900;
    font-size: 40px;
    letter-spacing: 1px;
    line-height: 1;
    text-transform: uppercase;
  }
  .contact__first { color: var(--brand-orange); }
  .contact__last { color: var(--brand-blue); }
  .contact__title {
    margin-top: 8px;
    font-size: 25px;
    color: var(--ink-grey);
    letter-spacing: 0.5px;
  }
  .contact__rule {
    width: 104px;
    height: 3px;
    background: var(--brand-orange);
    margin: 12px 0 20px;
  }
  .contact__list { list-style: none; }
  .contact__item {
    display: flex;
    align-items: center;
    gap: 14px;
    font-size: 25px;
    color: var(--ink-grey);
    letter-spacing: 0.5px;
    margin-bottom: 14px;
  }
  .contact__icon {
    width: 32px; height: 32px;
    background: var(--brand-blue);
    border-radius: 4px;
    display: flex; align-items: center; justify-content: center;
    flex-shrink: 0;
  }

  /* Back */
  .back__corner {
    position: absolute;
    left: 0; bottom: 0;
    width: 190px; height: 150px;
    background: var(--brand-orange);
    clip-path: polygon(0 100%, 0 20%, 60% 0, 100% 100%);
  }
  .back__name {
    position: absolute;
    left: 60px;
    top: 110px;
    font-weight: 900;
    font-size: 140px;
    line-height: 1;
    color: var(--paper);
  }
  .back__services {
    position: absolute;
    right: 60px;
    bottom: 140px;
    font-size: 22px;
    letter-spacing: 1px;
    color: var(--soft-white);
  }
  .back__url {
    position: absolute;
    right: 60px;
    bottom: 80px;
    font-weight: 700;
    font-size: 40px;
    letter-spacing: 1.5px;
    line-height: 1;
    color: var(--paper);
  }
</style>
</head>
<body>

<section class="card card--front">
  <div class="brand">
    <div class="brand__row">
      <span class="brand__square"></span>
      <span class="brand__name">Vextorial</span>
    </div>
    <p class="brand__tagline">developer of custom applications</p>
    <p class="brand__services">&amp; Bitcoin services for business</p>
  </div>

  <div class="contact">
    <h1 class="contact__name"><span class="contact__first">Dale</span> <span class="contact__last">Parker</span></h1>
    <p class="contact__title">Software Developer</p>
    <div class="contact__rule"></div>
    <ul class="contact__list">
      <li class="contact__item">
        <span class="contact__icon">
          <svg width="20" height="20" viewBox="0 0 24 24"><path fill="#fff" d="M6.6 10.8a15.1 15.1 0 0 0 6.6 6.6l2.2-2.2c.3-.3.7-.4 1-.2 1.1.4 2.3.6 3.6.6.6 0 1 .4 1 1V20c0 .6-.4 1-1 1A17 17 0 0 1 3 4c0-.6.4-1 1-1h3.5c.6 0 1 .4 1 1 0 1.3.2 2.5.6 3.6.1.3 0 .7-.2 1z"/></svg>
        </span>
        (888) 555-VXTRL
      </li>
      <li class="contact__item">
        <span class="contact__icon">
          <svg width="20" height="20" viewBox="0 0 24 24"><rect x="3" y="6" width="18" height="12" fill="none" stroke="#fff" stroke-width="2"/><path d="M3 6l9 7 9-7M3 18l7-6M21 18l-7-6" fill="none" stroke="#fff" stroke-width="2"/></svg>
        </span>
        dale@vextorial.com
      </li>
      <li class="contact__item">
        <span class="contact__icon">
          <svg width="20" height="20" viewBox="0 0 24 24"><path fill="#fff" d="M6 3l12 10h-6l3 7-2.5 1-3-7L6 18z"/></svg>
        </span>
        vextorial.com
      </li>
    </ul>
  </div>
</section>

<section class="card card--back">
  <div class="back__corner"></div>
  <p class="back__name">Vextorial</p>
  <p class="back__services">Custom software · Bitcoin education &amp; payments</p>
  <p class="back__url">vextorial.com</p>
</section>

</body>
</html>
```